Flyer Design for Wedding Showcase

We are a modern Australian Restaurant situated on the Swan River in Perth boasting beautiful city views. We require a DL size flyer one sided to promote our wedding open evening which we hold every year.

Heading: Corella Point Restaurant Wedding Showcase
19th September 2014 from 5pm to 8pm
Address: Corella Point Restaurant, 17 Brindle Parade, Wexton WA 6112
Contact for more information: 08 9561 7284

There is several suppliers showcasing every year and we also have cocktail food and wine tastings at the event. Clients will also have the opportunity to chat to the function coordinators from Corella Point Restaurant.

We would like a modern, elegant design with a warm feeling to it. Couples getting married should be able to relate and identify with this design.

Target Market(s)

Young couples looking to get married

Industry/Entity Type

Wedding

Colors
3276b5
cee9f5
85abd2
eea4c8

Requirements
Must have
• Must have the following blurb:
Corella Point Restaurant is Perth's premium wedding venue situated on the Swan River boasting beautiful views of the Perth city skyline.
Come and meet our team and some of our favorite wedding suppliers while enjoying this beautiful location and sampling some of the food and wine we offer.

Logo needs to be on flyer
Should not have
• hot pink

```html
<!DOCTYPE html>
<html lang="en">
<head>
<meta charset="utf-8">
<title>Wedding Showcase Flyer</title>
<link rel="stylesheet" href="https://fonts.googleapis.com/css2?family=Pinyon+Script&family=Cinzel:wght@400;700&family=Cormorant+Garamond:ital,wght@1,500&display=swap">
<style>
  :root {
    --paper: #ffffff;
    --plate: #f3f1f0;
    --sauce: #5a2e1c;
    --pear: #ead9a8;
    --river: #3276b5;
    --river-soft: #85abd2;
    --river-deep: #255c90;
    --mist: #cee9f5;
    --blush: #eea4c8;
    --ink-light: #ffffff;
  }
  * { margin: 0; padding: 0; box-sizing: border-box; }
  html, body {
    width: 1200px; height: 2400px; overflow: hidden;
    background: var(--paper);
  }
  .flyer {
    position: relative; width: 1200px; height: 2400px; overflow: hidden;
    background: var(--paper);
  }
  .dessert-photo {
    position: absolute; left: 0; top: 0; width: 1200px; height: 1040px;
    background:
      radial-gradient(ellipse 260px 220px at 520px 420px, var(--sauce) 0%, rgba(90,46,28,0.85) 55%, rgba(90,46,28,0) 100%),
      radial-gradient(ellipse 280px 180px at 760px 760px, var(--pear) 0%, rgba(234,217,168,0.7) 60%, rgba(234,217,168,0) 100%),
      linear-gradient(160deg, var(--paper) 0%, var(--plate) 60%, #e6e3e2 100%);
  }
  .ornament {
    position: absolute; background: var(--blush);
  }
  .ornament--top-left {
    left: 0; top: 0; width: 190px; height: 120px;
    border-radius: 0 0 110px 0;
  }
  .ornament--right {
    right: 0; top: 780px; width: 380px; height: 260px;
    border-radius: 240px 0 0 0;
  }
  .event-panel {
    position: absolute; left: 0; top: 1040px; width: 1200px; height: 1360px;
    background:
      radial-gradient(circle 60px at 1100px 90px, rgba(206,233,245,0.35), rgba(206,233,245,0)),
      radial-gradient(circle 80px at 1060px 520px, rgba(206,233,245,0.25), rgba(206,233,245,0)),
      radial-gradient(circle 70px at 120px 520px, rgba(206,233,245,0.22), rgba(206,233,245,0)),
      radial-gradient(circle 90px at 80px 1240px, rgba(206,233,245,0.22), rgba(206,233,245,0)),
      linear-gradient(180deg, var(--river) 0%, #4a88c2 55%, var(--river) 100%);
  }
  .brand {
    position: absolute; left: 0; top: 1082px; width: 1200px;
    display: flex; align-items: center; justify-content: center; gap: 18px;
    font-family: "Cinzel", serif; font-weight: 700; font-size: 34px; line-height: 40px;
    color: var(--mist); letter-spacing: 2px;
  }
  .brand-dot {
    width: 22px; height: 22px; border-radius: 50%; background: var(--blush);
  }
  .event-title {
    position: absolute; left: 0; top: 1150px; width: 1200px;
    font-family: "Pinyon Script", cursive; color: var(--ink-light);
    font-weight: 400; font-size: 200px; line-height: 210px;
  }
  .event-title span { display: block; }
  .event-title .line-one { padding-left: 150px; }
  .event-title .line-two { padding-left: 300px; }
  .blurb {
    position: absolute; left: 110px; top: 1610px; width: 980px; text-align: center;
    font-family: "Cormorant Garamond", serif; font-style: italic; font-weight: 500;
    font-size: 31px; line-height: 40px; color: var(--ink-light);
  }
  .blurb p + p { margin-top: 14px; }
  .date-band {
    position: absolute; left: 0; top: 1830px; width: 1200px; height: 140px;
    background: var(--river-deep);
    display: flex; flex-direction: column; align-items: center; justify-content: center;
    font-family: "Cinzel", serif; color: var(--ink-light); text-align: center;
  }
  .date-band .date { font-size: 46px; font-weight: 700; line-height: 54px; }
  .date-band .time { font-size: 40px; font-weight: 400; line-height: 46px; text-transform: lowercase; }
  .details {
    position: absolute; left: 0; top: 2010px; width: 1200px; text-align: center;
    font-family: "Cinzel", serif; color: var(--mist);
  }
  .details .label { font-size: 28px; line-height: 36px; font-weight: 400; }
  .details .value { font-size: 38px; line-height: 48px; font-weight: 700; }
  .details .address { width: 860px; margin: 0 auto; }
  .details .contact-label { margin-top: 24px; }
</style>
</head>
<body>
  <main class="flyer">
    <div class="dessert-photo" role="img" aria-label="Photograph of a sticky date pudding with caramel sauce, poached pear slices and cream on a white plate"></div>
    <div class="ornament ornament--top-left" role="img" aria-label="Blush pink flourish ornament in the top left corner"></div>
    <div class="ornament ornament--right" role="img" aria-label="Blush pink flourish ornament on the right edge"></div>

    <section class="event-panel"></section>

    <div class="brand">
      <span class="brand-dot"></span>
      <span class="brand-name">Corella Point Restaurant</span>
    </div>

    <h1 class="event-title">
      <span class="line-one">Wedding</span>
      <span class="line-two">Showcase</span>
    </h1>

    <div class="blurb">
      <p>Corella Point Restaurant is Perth's premium wedding venue situated on the Swan River boasting beautiful views of the Perth city skyline.</p>
      <p>Come and meet our team and some of our favorite wedding suppliers while enjoying this beautiful location and sampling some of the food and wine we offer.</p>
    </div>

    <div class="date-band">
      <p class="date">19th September 2014</p>
      <p class="time">from 5pm to 8pm</p>
    </div>

    <div class="details">
      <p class="label">Address:</p>
      <p class="value address">Corella Point Restaurant, 17 Brindle Parade, Wexton WA 6112</p>
      <p class="label contact-label">Contact for more information:</p>
      <p class="value phone">08 9561 7284</p>
    </div>
  </main>
</body>
</html>
```